BRANDEMEIER & BRANDEMEIER,LLP NEEDS A NEW LETTERHEAD DESIGN

a conservative yet contemporary layout befitting a long established
firm, consistent with the times, some form of logo so it catches ones attention, and is
admirable, but portrays integrity
Updates

I would like to approve #22066987 Please advise how to do this as it’s confusing on the site so I can approve payment for the designer

Target Market(s)

real estate investors and building management people

Industry/Entity Type

Law Firm

Font styles to use
Serif

Colors

Designer to choose colors to be used in the design.

Requirements
Must have
• some form of conservative logo

```html
<!DOCTYPE html>
<html lang="en">
<head>
<meta charset="utf-8">
<title>Brandemeier &amp; Brandemeier, LLP — Letterhead</title>
<link href="https://fonts.googleapis.com/css2?family=Cinzel:wght@500&family=Arimo:wght@400;700&display=swap" rel="stylesheet">
<style>
  :root {
    --backdrop: #c9cace;
    --paper: #f2f2f2;
    --ink: #2f2f38;
    --ink-soft: #55555c;
    --silver: #c2c2c5;
    --band-dark: #4a4850;
    --band-light: #b9b9bc;
  }
  html, body {
    margin: 0;
    padding: 0;
    width: 1200px;
    height: 1166px;
    overflow: hidden;
    background: var(--backdrop);
  }
  .letterhead {
    position: absolute;
    left: 214px;
    top: 69px;
    width: 788px;
    height: 1019px;
    background: var(--paper);
  }
  .brand-mark {
    position: absolute;
    left: 72px;
    top: 59px;
    width: 64px;
    height: 64px;
    border: 1.5px solid var(--silver);
    border-radius: 50%;
    box-sizing: border-box;
  }
  .firm-name {
    position: absolute;
    left: 146px;
    top: 74px;
    margin: 0;
    font-family: "Cinzel", serif;
    font-weight: 500;
    font-size: 17.5px;
    letter-spacing: 0.2px;
    color: var(--ink);
    white-space: nowrap;
  }
  .firm-tagline {
    position: absolute;
    left: 146px;
    top: 96px;
    margin: 0;
    font-family: "Cinzel", serif;
    font-weight: 500;
    font-size: 11.5px;
    letter-spacing: 0.3px;
    color: var(--ink-soft);
    white-space: nowrap;
  }
  .contact {
    position: absolute;
    left: 66px;
    top: 955px;
    margin: 0;
    font-family: "Arimo", sans-serif;
    font-size: 10px;
    line-height: 12.5px;
    color: var(--ink-soft);
    font-style: normal;
  }
  .contact b { color: var(--ink); }
  .website {
    position: absolute;
    right: 64px;
    top: 955px;
    margin: 0;
    font-family: "Arimo", sans-serif;
    font-size: 10px;
    letter-spacing: 3.2px;
    color: var(--ink-soft);
  }
  .footer-bands {
    position: absolute;
    left: 0;
    bottom: 0;
    width: 788px;
    height: 18px;
    display: block;
  }
</style>
</head>
<body>
  <main class="letterhead">
    <header>
      <span class="brand-mark" aria-hidden="true"></span>
      <h1 class="firm-name">BRANDEMEIER &amp; BRANDEMEIER, LLP</h1>
      <p class="firm-tagline">Attorneys and Counselors at Law</p>
    </header>
    <footer>
      <address class="contact">
        48 Harlow Street Suite 210, Brooklyn, New York 11201<br>
        <b>T:</b> (718) 555-0143 · <b>F:</b> (718)-555-0178 · <b>E:</b> info@bbrelaw.com
      </address>
      <p class="website">www.bbrelaw.com</p>
      <svg class="footer-bands" viewBox="0 0 788 18" aria-hidden="true">
        <polygon points="0,6 516,6 508,18 0,18" fill="var(--band-dark)"/>
        <polygon points="530,0 788,0 788,18 512,18" fill="var(--band-light)"/>
      </svg>
    </footer>
  </main>
</body>
</html>
```